Brightway Haus Inc. Business Card Design

Brightway Haus Inc. is in search of a great clean design for our business cards!

Looking to incorporate our full logo and watermark on side one (however, I am open to having the text and watermark separated within the design.)

On side two, I am looking to have contact information (Name, Position, Phone #, Email, Website (www.thebrightwayhaus.ca). Can have the logo and/or watermark as part of the design if applicable.

Please add tagline "Where Shine Counts" on either side 1 or 2. This tagline can be in a sans serif, serif or cursive font as long as it compliments overall design. Capitalization can be title or sentence case depending on how it fits within the design.

Get creative!! Looking for a clean, crisp, premium design! Looking for a glossy card finish with spot UV features when printed. Cards will also be printed with rounded corners. Standard dimensions (3.5 x 2).

Target Market(s)

B2B - primary clients are business owners or property management corporations. (residential jobs are few and far between)

Industry/Entity Type

Business

Contact Information for Business Card

- clean, crisp design
- double sided
- spot UV accents and glossy finish upon printing
- standard business card size (3.5 x 2) with rounded corners
- please see project description for requirements per side

Font styles to use
Sans Serif

Requirements
Must have
• - adequate bleeds with print ready files
• - cohesive design elements between side 1 & 2
• - spot UV elements (can be on both sides or just one, use your discretion)
• - colour pallet should match the logo file provided
• - incorporate tagline "where shine counts" (this tagline can be in a serif or sans serif font as long as it is complimentary to the overall design.
Nice to have
• - Premium elements with a clean design
Should not have
• - Please omit cartoon or whimsical like designs, think premium.
• - Colours should not stray from the pallet of the provided logo.

```html
<!DOCTYPE html>
<html lang="en">
<head>
<meta charset="utf-8">
<title>Brightway Haus Inc. Business Card</title>
<link rel="stylesheet" href="https://fonts.googleapis.com/css2?family=Source+Sans+3:wght@400;600;700&display=swap">
<style>
  :root {
    --backdrop: #e6e7ea;
    --card-white: #ffffff;
    --navy: #1b2252;
    --teal: #1fb5b9;
    --ink-grey: #5a5d66;
    --rule-grey: #6b6e76;
    --silver: #c9ccd3;
    --tag-white: #f3f4f8;
  }
  * { margin: 0; padding: 0; box-sizing: border-box; }
  html, body {
    width: 1200px;
    height: 960px;
    overflow: hidden;
    background: var(--backdrop);
    font-family: "Source Sans 3", "Myriad Pro", Arial, sans-serif;
  }
  .canvas { position: relative; width: 1200px; height: 960px; }

  .card {
    position: absolute;
    width: 600px;
    height: 343px;
    border-radius: 22px;
    box-shadow: 0 4px 10px rgba(0,0,0,0.18);
  }
  .card-front { left: 314px; top: 113px; background: var(--card-white); }
  .card-back  { left: 311px; top: 472px; background: var(--navy); }

  .brand {
    position: absolute;
    display: flex;
    align-items: center;
    gap: 8px;
    font-weight: 700;
    letter-spacing: -0.3px;
    white-space: nowrap;
  }
  .brand-square { display: block; width: 18px; height: 18px; }
  .card-front .brand {
    left: 60px; top: 155px;
    font-size: 24px;
    color: var(--navy);
  }
  .card-front .brand-square { background: var(--teal); }
  .card-back .brand {
    left: 0; right: 0; top: 148px;
    justify-content: center;
    font-size: 38px;
    color: var(--silver);
  }
  .card-back .brand-square { width: 28px; height: 28px; background: var(--silver); }

  .divider {
    position: absolute;
    left: 339px; top: 75px;
    width: 2px; height: 190px;
    background: var(--rule-grey);
  }
  .contact {
    position: absolute;
    left: 363px; top: 76px;
    color: var(--ink-grey);
    font-size: 15px;
    line-height: 19px;
  }
  .contact-name {
    color: var(--teal);
    font-weight: 700;
    font-size: 17px;
    line-height: 21px;
  }
  .contact-title {
    color: var(--navy);
    font-size: 17px;
    line-height: 21px;
    margin-bottom: 5px;
  }
  .contact-address { margin-bottom: 6px; }

  .tagline {
    position: absolute;
    left: 100px; right: 100px; top: 276px;
    display: flex;
    align-items: center;
    gap: 2px;
    color: var(--tag-white);
    font-weight: 600;
    font-size: 18px;
    white-space: nowrap;
  }
  .tagline-rule { flex: 1; height: 1px; }
  .tagline-rule.left  { background: linear-gradient(to right, rgba(255,255,255,0), rgba(255,255,255,0.9)); }
  .tagline-rule.right { background: linear-gradient(to left, rgba(255,255,255,0), rgba(255,255,255,0.9)); }
</style>
</head>
<body>
<main class="canvas">
  <section class="card card-front">
    <div class="brand"><span class="brand-square"></span>Brightway Haus Inc.</div>
    <div class="divider"></div>
    <div class="contact">
      <p class="contact-name">MARA ELLISON</p>
      <p class="contact-title">CEO/FOUNDER</p>
      <p class="contact-address">214 Harbourview Road<br>Halifax, Nova Scotia B3H 2Y9</p>
      <p>(P) 902 555 0148</p>
      <p>(M) 902 555 0193</p>
      <p>(F) 902 555 0176</p>
      <p>hello@thebrightwayhaus.ca</p>
      <p>www.thebrightwayhaus.ca</p>
    </div>
  </section>

  <section class="card card-back">
    <div class="brand"><span class="brand-square"></span>Brightway Haus Inc.</div>
    <div class="tagline">
      <span class="tagline-rule left"></span>
      <span>Where Shine Counts</span>
      <span class="tagline-rule right"></span>
    </div>
  </section>
</main>
</body>
</html>
```